Candle Rental Business seeks new website design

We need a new website design for a Candle hire business. The business rents out pillar candles for events such as weddings and corporate events. Our main target market is weddings. The business name is Hire a Lantern. The business name does not have a logo design.

We would like a website that is light in colours and creates a warm atmosphere. The design needs to be elegant and upmarket. There are different size candles that we hire out, ranging from 10cm diameter to 20cm diameter, flat, tall etc. All our candles are white in colour. Its just the size that differs.

We would also like to include a section for hiring out decor such as glassvases, candlebras, overlays and chairs sachets, chair covers. However, this is not the businesses main focus but an additional offering to customers.

Target Market(s)

Wedding venues and brides. Corporate events. School dances.

Industry/Entity Type

Hospitality

Logo Text

Hire a Lantern

Number of Pages Required

1 page

Font styles to use
Sans Serif
Script

Requirements
Must have
• Pictures of pillar candles. Plain white candles. The website must centre around candles.
Nice to have
• Different examples of candle centrepieces
Should not have
• Pictures must not be of brides. Pictures of surrounding is perferable.

```html
<!DOCTYPE html>
<html lang="en">
<head>
<meta charset="utf-8">
<title>Hire a Lantern</title>
<link href="https://fonts.googleapis.com/css2?family=Lato:wght@400;700&family=Questrial&family=Russo+One&display=swap" rel="stylesheet">
<style>
:root{
  --orange:#f47a14;
  --amber:#fbb116;
  --green:#7d9a3b;
  --beige:#f5f2e6;
  --grey-band:#ececec;
  --text:#555;
  --heading:#222;
  --dark:#2f2f2f;
  --white:#fff;
  --line:#ccc;
}
*{box-sizing:border-box;margin:0;padding:0}
html,body{width:1200px;height:2727px;overflow:hidden;background:var(--white)}
body{font-family:'Lato',sans-serif;color:var(--text);position:relative}
a{color:inherit;text-decoration:none}

/* header */
.site-header{height:86px;position:relative}
.brand{position:absolute;left:80px;top:12px;display:flex;align-items:center;gap:14px}
.brand-mark{width:26px;height:54px;background:var(--orange);border-radius:4px}
.brand-name{font-family:'Questrial',sans-serif;font-size:38px;color:var(--heading)}
.account-links{position:absolute;right:80px;top:12px;display:flex;gap:30px;font-size:13px;color:#666}
.account-links span{display:flex;align-items:center;gap:7px}
.account-links i{display:inline-block;width:12px;height:12px;border:1.5px solid #888;border-radius:2px}
.main-nav{position:absolute;right:78px;top:50px;display:flex;gap:20px;font-size:15px;color:var(--heading)}
.main-nav a{padding:4px 8px}
.main-nav .active{border:1.5px solid var(--orange);color:var(--orange)}

/* hero */
.hero{height:534px;position:relative;overflow:hidden}
.hero-photo{position:absolute;inset:0;background:
  radial-gradient(ellipse 260px 300px at 730px 280px,#f7e2b4 0%,#d9b68c 25%,rgba(120,90,160,0) 70%),
  radial-gradient(ellipse 500px 260px at 400px 330px,rgba(240,200,150,.55),rgba(0,0,0,0) 70%),
  linear-gradient(180deg,#4a3f8a 0%,#6e62c0 40%,#3b3260 75%,#1d1830 100%)}
.hero-arrow{position:absolute;top:240px;width:30px;height:50px}
.hero-arrow.prev{left:24px}
.hero-arrow.next{right:24px}
.hero-tagline{position:absolute;left:0;right:0;bottom:0;height:56px;background:linear-gradient(90deg,rgba(244,122,20,0) 0%,var(--orange) 12%,var(--orange) 88%,rgba(244,122,20,0) 100%);display:flex;align-items:center;justify-content:center;font-family:'Russo One',sans-serif;font-size:27px;color:var(--white);letter-spacing:.5px}

/* about */
.about{height:282px;text-align:center;padding-top:46px}
.section-title{font-family:'Questrial',sans-serif;font-size:41px;color:var(--heading);font-weight:400}
.about p{width:1040px;margin:18px auto 0;font-size:13.5px;line-height:26px}
.read-more-link{display:inline-block;margin-top:22px;color:var(--orange);text-decoration:underline;font-size:15px}

/* services */
.services{height:622px;background:var(--beige);position:relative}
.card{position:absolute;background:var(--white)}
.card h3{font-family:'Questrial',sans-serif;font-weight:400;font-size:25px;color:var(--heading)}
.card p{font-size:13.5px;line-height:26px;margin-top:8px}
.btn{display:inline-block;background:var(--green);color:var(--white);font-size:12px;padding:8px 16px}
.photo{display:block}
.card-hire{left:96px;top:58px;width:382px;height:500px;padding:16px 18px}
.card-hire .photo{width:346px;height:238px;background:linear-gradient(160deg,#d8d2c4,#eeeae2 40%,#b0c6cc 75%,#4a8fae)}
.card-hire h3{margin-top:10px}
.card-hire .btn{margin-top:12px}
.card-wide{left:498px;width:615px;height:240px;padding:12px 18px;display:flex;gap:24px}
.card-wide .body{flex:1}
.card-wide .btn{margin-top:12px}
.card-personal{top:58px}
.card-decor{top:318px}
.card-wide .photo{width:204px;height:204px;flex:none;margin-top:6px}
.card-personal .photo{background:linear-gradient(150deg,#ece9e6,#f4e3e6 50%,#c9a4b4)}
.card-decor .photo{background:radial-gradient(circle at 50% 70%,#e6e2a0,#8a9a4a 35%,#5a3a2a 80%)}

/* how it works */
.how{height:477px;text-align:center;padding-top:52px;position:relative}
.step{position:absolute;width:200px;text-align:center}
.step .disc{width:148px;height:148px;border-radius:50%;margin:0 auto;display:flex;align-items:center;justify-content:center}
.disc.orange{background:var(--orange)}
.disc.amber{background:var(--amber)}
.step span{display:block;margin-top:22px;font-size:22px;line-height:29px;color:#666}
.flow-arrow{position:absolute}

/* decor */
.decor{height:383px;background:var(--grey-band);text-align:center;padding-top:50px}
.decor-tiles{display:flex;gap:7px;justify-content:center;margin-top:48px}
.tile{width:255px;height:187px;position:relative;display:flex;align-items:center;justify-content:center}
.tile::after{content:"";position:absolute;inset:10px;border:1.5px solid rgba(255,255,255,.8)}
.tile b{position:relative;z-index:1;color:var(--white);font-size:23px;line-height:30px;text-shadow:0 1px 3px rgba(0,0,0,.6)}
.tile-vases{background:linear-gradient(180deg,#3a3028,#6e5c48 50%,#2a221c)}
.tile-bras{background:linear-gradient(180deg,#6a5f4a,#a79a7e 50%,#574d3c)}
.tile-overlays{background:linear-gradient(180deg,#3b3b38,#8c8a84 50%,#2b2b28)}
.tile-covers{background:linear-gradient(180deg,#2a2a2a,#a78890 50%,#4a3a3e)}

/* footer */
.site-footer{height:295px;background:var(--beige);position:relative;font-size:12.5px}
.footer-col{position:absolute;top:36px}
.footer-col h4{font-weight:400;font-size:14px;color:var(--heading);padding-bottom:8px;border-bottom:1px solid #d8d4c6;margin-bottom:14px}
.quick-links{left:80px;width:105px}
.quick-links li{list-style:none;height:49px;padding-left:18px;position:relative;color:#555}
.quick-links li::before{content:"";position:absolute;left:2px;top:5px;width:5px;height:5px;border:1px solid #777;border-radius:50%}
.contact{left:303px;width:215px}
.contact div{display:flex;gap:14px;margin-bottom:24px;line-height:19px}
.contact svg{flex:none}
.inquiry{left:652px;width:238px}
.inquiry .field{border:1px solid #555;background:var(--white);height:28px;margin-bottom:9px;padding:4px 6px;font-size:11px;color:#666}
.inquiry .field.msg{height:48px}
.inquiry .submit{background:var(--orange);color:var(--white);text-align:center;height:32px;line-height:32px;font-size:14px}
.follow{left:1002px;width:118px}
.follow div{display:flex;align-items:center;gap:11px;height:43px;font-size:12px}
.follow i{width:32px;height:32px;border-radius:50%;display:inline-block}
.bottom-bar{height:47px;background:var(--dark);color:#ddd;font-size:13px;display:flex;align-items:center;justify-content:space-between;padding:0 80px}
.cards{display:flex;align-items:center;gap:10px}
.cards i{width:27px;height:17px;background:#eee;border-radius:2px;display:inline-block}
</style>
</head>
<body>

<header class="site-header">
  <div class="brand"><span class="brand-mark"></span><span class="brand-name">Hire a Lantern</span></div>
  <div class="account-links"><span><i></i>log In</span><span><i></i>Register</span></div>
  <nav class="main-nav"><a class="active">Home</a><a>About Us</a><a>Our Products</a><a>Contact Us</a></nav>
</header>

<section class="hero">
  <div class="hero-photo" role="img" aria-label="Reception table lit by tall pillar candles in glass cylinders under violet light"></div>
  <svg class="hero-arrow prev" viewBox="0 0 30 50"><polyline points="26,3 4,25 26,47" fill="none" stroke="#fff" stroke-width="2"/></svg>
  <svg class="hero-arrow next" viewBox="0 0 30 50"><polyline points="4,3 26,25 4,47" fill="none" stroke="#fff" stroke-width="2"/></svg>
  <div class="hero-tagline">WE DESIGN, MANUFACTURE &amp; PERSONALISE DECORATIVE CANDLES</div>
</section>

<section class="about">
  <h2 class="section-title">About Us</h2>
  <p>We are a family owned and operated company and began making decorative candles for all occasions.&nbsp; All of our candles are individually hand made in our candle studio, situated in Kauri Bay, outside Harbourton.&nbsp; Our wax is local and of a very high quality, and dripless! Our wax is also made with a high melting point, which means it will not melt or bend in hot temperatures.</p>
  <a class="read-more-link">Read More</a>
</section>

<section class="services">
  <article class="card card-hire">
    <div class="photo" role="img" aria-label="White pillar candle centrepiece with blue glass pebbles on a dining table"></div>
    <h3>Hire Candles</h3>
    <p>Do you love using candles for your events but tired of sorting old used candles or buying expensive the candles. Believe it or not you can now rent lorem is candles.All our candles come in different sizes and heights.You can add the ambience of.</p>
    <a class="btn">Read More</a>
  </article>
  <article class="card card-wide card-personal">
    <div class="body">
      <h3>Personalised Candles</h3>
      <p>Hire a Lantern provides the opportunity to give a thoughtful, meaningful gift at a friendly price point. This unique gift conveys the time and care you put into creating it. The recipient will enjoy the beautiful presentation and be reminded of the sentiment...</p>
      <a class="btn">Read More</a>
    </div>
    <div class="photo" role="img" aria-label="Two personalised candles in glass jars with pink labels"></div>
  </article>
  <article class="card card-wide card-decor">
    <div class="body">
      <h3>Décor Hire</h3>
      <p>We hire a selection of overlays, chair sachets and chair covers as well as glassware and candelabras to compliment your décor.</p>
      <a class="btn">Read More</a>
    </div>
    <div class="photo" role="img" aria-label="Table centrepiece of white flowers around a glass candle holder"></div>
  </article>
</section>

<section class="how">
  <h2 class="section-title">How It Works</h2>
  <svg class="flow-arrow" style="left:250px;top:150px" width="110" height="40" viewBox="0 0 110 40"><path d="M2 30 Q50 0 100 20" fill="none" stroke="#ccc" stroke-width="2"/><polyline points="88,10 102,21 88,28" fill="none" stroke="#ccc" stroke-width="2"/></svg>
  <svg class="flow-arrow" style="left:550px;top:330px" width="110" height="40" viewBox="0 0 110 40"><path d="M2 20 Q50 40 100 10" fill="none" stroke="#ccc" stroke-width="2"/><polyline points="86,6 102,9 94,22" fill="none" stroke="#ccc" stroke-width="2"/></svg>
  <svg class="flow-arrow" style="left:846px;top:150px" width="110" height="40" viewBox="0 0 110 40"><path d="M2 25 Q50 2 100 20" fill="none" stroke="#ccc" stroke-width="2"/><polyline points="88,10 102,21 88,28" fill="none" stroke="#ccc" stroke-width="2"/></svg>

  <div class="step" style="left:54px;top:180px">
    <div class="disc orange"><svg width="46" height="80" viewBox="0 0 46 80" fill="#fff"><path d="M23 2 C30 12 30 20 23 22 C16 20 16 12 23 2Z"/><rect x="5" y="28" width="36" height="50" rx="4"/></svg></div>
    <span>Choose your<br>Candle</span>
  </div>
  <div class="step" style="left:350px;top:180px">
    <div class="disc amber"><svg width="64" height="80" viewBox="0 0 64 80" fill="#fff"><rect x="16" y="4" width="12" height="44" rx="6"/><path d="M10 42 h44 a6 6 0 0 1 6 6 v14 a16 16 0 0 1 -16 16 h-20 a14 14 0 0 1 -14 -14 z"/></svg></div>
    <span>Book your<br>Candle</span>
  </div>
  <div class="step" style="left:650px;top:180px">
    <div class="disc orange"><svg width="84" height="60" viewBox="0 0 84 60"><rect x="4" y="10" width="76" height="42" rx="4" fill="#fff" transform="rotate(-8 42 31)"/><circle cx="42" cy="31" r="11" fill="var(--orange)"/></svg></div>
    <span>Make<br>payment</span>
  </div>
  <div class="step" style="left:945px;top:176px">
    <div class="disc amber"><svg width="60" height="86" viewBox="0 0 60 86" fill="#fff"><path d="M30 2 C36 11 36 18 30 20 C24 18 24 11 30 2Z"/><rect x="18" y="24" width="24" height="40" rx="3"/><path d="M4 66 h52 l-8 10 h-36 z"/><rect x="20" y="76" width="20" height="6"/></svg></div>
    <span>Light Up<br>Your Event</span>
  </div>
</section>

<section class="decor">
  <h2 class="section-title">Our Hiring Out Decor</h2>
  <div class="decor-tiles">
    <div class="tile tile-vases" role="img" aria-label="Candles glowing inside glass vases"><b>Glass Vases</b></div>
    <div class="tile tile-bras" role="img" aria-label="Glass candelabras on a table"><b>Candle Bras</b></div>
    <div class="tile tile-overlays" role="img" aria-label="Lace chair sachet tied in a bow"><b>Overlays &amp;<br>Chairs Sachets</b></div>
    <div class="tile tile-covers" role="img" aria-label="Row of chairs with pink sashes"><b>Chair Covers</b></div>
  </div>
</section>

<footer class="site-footer">
  <div class="footer-col quick-links">
    <h4>Quick Links</h4>
    <ul><li>Home</li><li>About Us</li><li>Our Products</li><li>Contact Us</li></ul>
  </div>
  <div class="footer-col contact">
    <h4>Contact Details</h4>
    <div><svg width="20" height="24" viewBox="0 0 20 24"><path d="M10 2 a7 7 0 0 1 7 7 c0 6 -7 13 -7 13 s-7 -7 -7 -13 a7 7 0 0 1 7 -7z" fill="none" stroke="#777" stroke-width="1.6"/><circle cx="10" cy="9" r="2.5" fill="#777"/></svg>1/23 Lorem Ips Dolo, Consecer<br>wererr Nonuy - 12345</div>
    <div style="margin-top:6px"><svg width="20" height="22" viewBox="0 0 20 22"><path d="M5 2 l4 5 -2 3 c1 3 3 5 6 6 l3 -2 4 4 -3 3 c-8 0 -14 -7 -15 -15z" fill="none" stroke="#777" stroke-width="1.5"/></svg><span style="font-size:14px">123-456-7890</span></div>
    <div style="margin-top:10px"><svg width="20" height="16" viewBox="0 0 20 16"><rect x="1" y="2" width="18" height="12" fill="none" stroke="#777" stroke-width="1.5"/><polyline points="1,2 10,9 19,2" fill="none" stroke="#777" stroke-width="1.5"/></svg>hello@hirealantern.com</div>
  </div>
  <div class="footer-col inquiry">
    <h4>Quick Inquiry</h4>
    <div class="field">Name</div>
    <div class="field">Phone</div>
    <div class="field msg">Message</div>
    <div class="submit">Submit</div>
  </div>
  <div class="footer-col follow">
    <h4>Follow Us</h4>
    <div><i style="background:#3b5998"></i><span style="color:#3b5998">Facepage</span></div>
    <div><i style="background:#3aa9e0"></i><span style="color:#3aa9e0">Chatter</span></div>
    <div><i style="background:#2a78b8"></i><span style="color:#2a78b8">Workline</span></div>
    <div><i style="background:#d34836"></i><span style="color:#d34836">Globe Plus</span></div>
  </div>
</footer>

<div class="bottom-bar">
  <span>Copyright © 2016 Hire a Lantern. All Rights Reserved.</span>
  <span class="cards">We Accept: <i></i><i></i><i></i><i></i></span>
</div>

</body>
</html>
```